Social Media Graphics - Oakline Push REVISED

Create 6-7 individual social media graphics (square size) to encourage folks to join our online course called:

The Harvest Ledger Circle
How to Launch a Multi-Million Business From Scratch
Sign Up Today!

IMPORTANT: Make the largest and most prominent text on the graphic be: How to Launch a Multi-Million Business From Scratch

For the color scheme of the graphics, let's try a blue color palette; make sure the graphics appeal to both men and women

Make sure each graphic contains 1 of the 3 pics attached (crop pic as needed); and make sure one of the graphics is all TEXT only.

Target Market(s)

men and women looking to start a business

Industry/Entity Type

Entrepreneurship

Colors
0054AA
0677BA
7BADD7
CADEEF
E8F1F8

Requirements
Must have
• All the text and use the 3 pics provided; one graphic can be all text; Simple, modern design that's easy to read

```html
<!DOCTYPE html>
<html lang="en">
<head>
<meta charset="utf-8">
<title>The Harvest Ledger Circle – Social Graphics</title>
<link rel="stylesheet" href="https://fonts.googleapis.com/css2?family=Poppins:wght@600;800&family=Montserrat:wght@800&family=Oswald:wght@500&family=Righteous&family=Krona+One&family=Cormorant+Garamond:wght@500&display=swap">
<style>
  :root {
    --page: #272727;
    --blue-deep: #0054AA;
    --blue: #0677BA;
    --blue-soft: #7BADD7;
    --blue-pale: #CADEEF;
    --blue-mist: #E8F1F8;
    --white: #FFFFFF;
    --ink: #1C1C1C;
    --orange: #F7941D;
    --navy: #0B3F86;
  }
  * { margin: 0; padding: 0; box-sizing: border-box; }
  html, body { width: 877px; height: 1200px; overflow: hidden; background: var(--page); }
  .sheet { position: relative; width: 877px; height: 1200px; }
  .tile { position: absolute; width: 330px; height: 330px; overflow: hidden; }
  .tile-a { left: 88px; top: 66px; }
  .tile-b { left: 470px; top: 66px; }
  .tile-c { left: 91px; top: 424px; }
  .tile-d { left: 473px; top: 424px; }
  .tile-e { left: 91px; top: 786px; }
  .tile-f { left: 470px; top: 789px; }

  .photo { position: absolute; left: 0; top: 0; width: 100%; }
  .shape { position: absolute; left: 0; width: 330px; }

  .stack { position: absolute; left: 0; width: 100%; text-align: center; }
  .kicker { font-family: "Righteous", sans-serif; font-size: 14px; color: var(--ink); letter-spacing: .3px; text-transform: uppercase; }
  .kicker-cond { font-family: "Oswald", sans-serif; font-weight: 500; font-size: 18px; text-transform: uppercase; }
  .headline { font-family: "Poppins", sans-serif; font-weight: 800; font-size: 19.5px; line-height: 25px; text-transform: uppercase; letter-spacing: -.2px; white-space: nowrap; margin-top: 8px; }
  .headline .accent { color: var(--orange); }
  .band { position: absolute; left: 0; bottom: 0; width: 100%; height: 42px; display: flex; align-items: center; justify-content: center; text-transform: uppercase; }
  .band-wide { font-family: "Montserrat", sans-serif; font-weight: 800; font-size: 19px; letter-spacing: 3px; color: var(--white); background: var(--blue-deep); }
  .band-light { font-family: "Poppins", sans-serif; font-weight: 800; font-size: 19px; color: var(--blue); background: var(--blue-mist); }

  .pill { position: absolute; display: flex; align-items: center; justify-content: center; border-radius: 16px; white-space: nowrap; text-transform: uppercase; }
  .left-head { position: absolute; left: 16px; font-family: "Poppins", sans-serif; font-weight: 600; font-size: 19.5px; line-height: 27.5px; text-transform: uppercase; color: var(--white); white-space: nowrap; }
  .cta-pill { font-family: "Poppins", sans-serif; font-weight: 800; font-size: 19px; }

  .serif-head { position: absolute; left: 0; top: 82px; width: 100%; text-align: center; font-family: "Cormorant Garamond", serif; font-weight: 500; font-size: 33px; line-height: 37.5px; color: var(--white); text-transform: uppercase; }
</style>
</head>
<body>
<main class="sheet">

  <!-- Graphic 1 -->
  <section class="tile tile-a" style="background: var(--white);">
    <div class="photo" role="img" aria-label="Photo of the two course hosts smiling against a blue backdrop" style="height: 170px; background: linear-gradient(180deg, var(--blue) 0%, var(--blue-deep) 100%);"></div>
    <svg class="shape" style="top: 140px;" width="330" height="40" viewBox="0 0 330 40"><path d="M0 28 Q165 -8 330 28 L330 40 L0 40 Z" fill="var(--white)"/></svg>
    <div class="stack" style="top: 170px;">
      <p class="kicker">The Harvest Ledger Circle</p>
      <h2 class="headline" style="color: var(--blue-deep);">How to launch a<br><span class="accent">Multi-Million Business</span><br>From Scratch</h2>
    </div>
    <div class="band band-wide">Sign up today!</div>
  </section>

  <!-- Graphic 2 -->
  <section class="tile tile-b" style="background: var(--blue-deep);">
    <div class="photo" role="img" aria-label="Photo of the two course hosts in dark and denim outfits on white" style="height: 160px; background: linear-gradient(180deg, var(--white) 0%, var(--blue-mist) 100%);"></div>
    <svg class="shape" style="top: 134px;" width="330" height="30" viewBox="0 0 330 30"><path d="M0 4 Q165 38 330 4 L330 30 L0 30 Z" fill="var(--blue-deep)"/></svg>
    <div class="stack" style="top: 171px;">
      <p class="kicker kicker-cond" style="color: var(--white);">The Harvest Ledger Circle</p>
      <h2 class="headline" style="color: var(--white); margin-top: 3px;">How to launch a<br>Multi-Million Business<br>From Scratch</h2>
    </div>
    <div class="band band-light">Sign up today!</div>
  </section>

  <!-- Graphic 3 -->
  <section class="tile tile-c" style="background: linear-gradient(180deg, var(--blue-deep) 0%, #0A56AE 100%);">
    <div role="img" aria-label="Photo of the two course hosts standing together" style="position: absolute; left: 80px; top: 14px; width: 168px; height: 130px; background: linear-gradient(180deg, #0B4E9C 0%, #1C2B45 100%); border-radius: 40px 40px 0 0;"></div>
    <div class="pill kicker-cond" style="left: 14px; top: 144px; width: 222px; height: 30px; background: var(--blue-mist); color: var(--blue-deep); font-size: 17px;">The Harvest Ledger Circle</div>
    <h2 class="left-head" style="top: 182px;">How to launch a<br>Multi-Million&nbsp; Business<br>From Scratch</h2>
    <div class="pill cta-pill" style="left: 14px; top: 276px; width: 206px; height: 35px; background: var(--blue-mist); color: var(--blue);">Sign up today!</div>
  </section>

  <!-- Graphic 4 -->
  <section class="tile tile-d">
    <div class="photo" role="img" aria-label="Close photo of the two course hosts in pink and black, smiling" style="height: 330px; background: linear-gradient(100deg, #C9415E 0%, #8E2F45 45%, #1E1B1D 60%, #141414 100%);"></div>
    <div class="pill kicker-cond" style="left: 14px; top: 144px; width: 210px; height: 30px; background: rgba(232,241,248,.8); color: var(--blue-deep); font-size: 17px;">The Harvest Ledger Circle</div>
    <h2 class="left-head" style="top: 182px;">How to launch a<br>Multi-Million&nbsp; Business<br>From Scratch</h2>
    <div class="pill cta-pill" style="left: 16px; top: 278px; width: 214px; height: 37px; background: linear-gradient(90deg, var(--navy), var(--blue-deep)); color: var(--white); border-radius: 18px;">Sign up today!</div>
  </section>

  <!-- Graphic 5: text only -->
  <section class="tile tile-e" style="background: var(--blue-deep);">
    <div class="pill" style="left: 22px; top: 34px; width: 289px; height: 33px; background: var(--blue-mist); color: var(--blue-deep); font-family: 'Krona One', sans-serif; font-size: 11.5px;">The Harvest Ledger Circle</div>
    <h2 class="serif-head">How to launch<br>a Multi-Million<br>Business from<br>Scratch</h2>
    <div class="pill" style="left: 45px; top: 257px; width: 244px; height: 46px; border-radius: 23px; background: var(--blue-mist); color: var(--blue); font-family: 'Poppins', sans-serif; font-weight: 600; font-size: 21px; letter-spacing: .5px;">Sign up today!</div>
  </section>

  <!-- Graphic 6 -->
  <section class="tile tile-f" style="background: var(--white);">
    <div class="photo" role="img" aria-label="Photo of the two course hosts speaking on stage with a microphone" style="height: 170px; background: linear-gradient(180deg, #5A4A3E 0%, #8A7664 50%, #B7A48C 100%);"></div>
    <svg class="shape" style="top: 140px;" width="330" height="40" viewBox="0 0 330 40"><path d="M0 28 Q165 -8 330 28 L330 40 L0 40 Z" fill="var(--white)"/></svg>
    <div class="stack" style="top: 170px;">
      <p class="kicker">The Harvest Ledger Circle</p>
      <h2 class="headline" style="color: var(--blue-deep);">How to launch a<br><span class="accent">Multi-Million Business</span><br>From Scratch</h2>
    </div>
    <div class="band band-wide" style="background: linear-gradient(90deg, var(--blue-deep), var(--blue));">Sign up today!</div>
  </section>

</main>
</body>
</html>
```